Diagram of Hollowmere’s history for website

This project is to design the attached diagram along the lines of the attached image but in our branding - style guide attached. The diagram will be going on the Hollowmere website - www.hollowmere.au.

```html
<!DOCTYPE html>
<html lang="en">
<head>
<meta charset="utf-8">
<title>Hollowmere – Our History</title>
<link rel="stylesheet" href="https://fonts.googleapis.com/css2?family=Poppins:wght@400;600&display=swap">
<style>
  :root{
    --bg:#ffffff;
    --ink:#333333;
    --body:#3a3a3a;
    --bar:#b9cdcd;
    --y2017:#667e82;
    --y2018:#7f9ea5;
    --y2019:#58705c;
    --y2021:#6e9170;
    --y2022:#ab8a7c;
    --y2023:#d4a994;
  }
  html,body{margin:0;padding:0;overflow:hidden;background:var(--bg);}
  .canvas{position:relative;width:1200px;height:708px;overflow:hidden;background:var(--bg);font-family:"Poppins",sans-serif;}
  .timeline-art{position:absolute;left:0;top:0;}
  .brand{position:absolute;left:100px;top:76px;display:flex;align-items:center;gap:7px;font-weight:600;font-size:15px;color:var(--y2017);}
  .brand-dot{width:12px;height:12px;border-radius:50%;background:var(--y2023);}
  .page-title{position:absolute;left:79px;top:152px;margin:0;font-size:24px;font-weight:600;color:var(--ink);letter-spacing:0.1px;}
  .event{position:absolute;width:150px;}
  .event h3{margin:0;font-size:17px;line-height:17px;font-weight:600;white-space:nowrap;}
  .event p{margin:6px 0 0;font-size:9px;line-height:10.6px;color:var(--body);}
  .year{position:absolute;margin:0;font-size:20px;line-height:24px;font-weight:600;}
  .c2017{color:var(--y2017);} .c2018{color:var(--y2018);} .c2019{color:var(--y2019);}
  .c2021{color:var(--y2021);} .c2022{color:var(--y2022);} .c2023{color:var(--y2023);}
</style>
</head>
<body>
<div class="canvas">
  <svg class="timeline-art" width="1200" height="708" viewBox="0 0 1200 708" aria-hidden="true">
    <rect x="79" y="362" width="1036" height="15" fill="var(--bar)"/>
    <polygon points="1114,353 1131,370 1114,387" fill="var(--bar)"/>
    <line x1="79" y1="370" x2="79" y2="507" stroke="var(--y2017)" stroke-width="1.2"/>
    <line x1="250" y1="267" x2="250" y2="370" stroke="var(--y2018)" stroke-width="1.2"/>
    <line x1="419" y1="370" x2="419" y2="481" stroke="var(--y2019)" stroke-width="1.2"/>
    <line x1="588" y1="267" x2="588" y2="370" stroke="var(--y2021)" stroke-width="1.2"/>
    <line x1="757" y1="370" x2="757" y2="639" stroke="var(--y2022)" stroke-width="1.2"/>
    <line x1="926" y1="64" x2="926" y2="370" stroke="var(--y2023)" stroke-width="1.2"/>
    <g stroke="#fff" stroke-width="2">
      <circle cx="79" cy="370" r="11.5" fill="var(--y2017)"/>
      <circle cx="79" cy="507" r="11.5" fill="var(--y2017)"/>
      <circle cx="250" cy="267" r="11.5" fill="var(--y2018)"/>
      <circle cx="250" cy="370" r="11.5" fill="var(--y2018)"/>
      <circle cx="419" cy="370" r="11.5" fill="var(--y2019)"/>
      <circle cx="419" cy="481" r="11.5" fill="var(--y2019)"/>
      <circle cx="588" cy="267" r="11.5" fill="var(--y2021)"/>
      <circle cx="588" cy="370" r="11.5" fill="var(--y2021)"/>
      <circle cx="757" cy="370" r="11.5" fill="var(--y2022)"/>
      <circle cx="757" cy="639" r="11.5" fill="var(--y2022)"/>
      <circle cx="926" cy="64" r="11.5" fill="var(--y2023)"/>
      <circle cx="926" cy="106" r="11.5" fill="var(--y2023)"/>
      <circle cx="926" cy="178" r="11.5" fill="var(--y2023)"/>
      <circle cx="926" cy="232" r="11.5" fill="var(--y2023)"/>
      <circle cx="926" cy="287" r="11.5" fill="var(--y2023)"/>
      <circle cx="926" cy="370" r="11.5" fill="var(--y2023)"/>
    </g>
  </svg>

  <div class="brand"><span class="brand-dot"></span>Hollowmere</div>
  <h1 class="page-title">Our History</h1>

  <div class="event c2017" style="left:99px;top:385px;width:140px;">
    <h3>Hollowmere<br>Commences</h3>
    <p>Maren started the business with 25 years’ experience working for government &amp; non-government disability &amp;community services. Our first office is in Preston</p>
  </div>
  <div class="event c2017" style="left:99px;top:500px;">
    <h3>NDIS Provider</h3>
    <p>Hollowmere becomes a NDIS<br>Registered provider</p>
  </div>
  <p class="year c2017" style="left:99px;top:552px;">2017</p>

  <div class="event c2018" style="left:277px;top:255px;width:130px;">
    <h3>Clinic Expansion</h3>
    <p>Hollowmere moves offices twice in Preston due to growth &amp; expansion.<br>Clinic established</p>
  </div>
  <p class="year c2018" style="left:277px;top:334px;">2018</p>

  <div class="event c2019" style="left:442px;top:385px;">
    <h3>Move to<br>Alphington</h3>
    <p>Hollowmere moves to Alphington due to further growth &amp; expansion</p>
  </div>
  <p class="year c2019" style="left:443px;top:469px;">2019</p>

  <div class="event c2021" style="left:616px;top:255px;width:172px;">
    <h3>Fair-Impact Co.</h3>
    <p>Hollowmere becomes an accredited Fair-Impact Company having met the highest standards of environmental, social &amp; community performance</p>
  </div>
  <p class="year c2021" style="left:616px;top:334px;">2021</p>

  <div class="event c2022" style="left:781px;top:385px;width:140px;">
    <h3>Telcova Best<br>of Business</h3>
    <p>Hollowmere wins the Telcova Best of Business Award (Vic) for building communities</p>
  </div>
  <div class="event c2022" style="left:781px;top:480px;">
    <h3>Move to Coburg</h3>
    <p>Hollowmere moves to a<br>larger premises in<br>Coburg</p>
  </div>
  <div class="event c2022" style="left:781px;top:549px;">
    <h3>Partnership</h3>
    <p>Partnerships established with Tarawa Inclusive Learning School &amp; Wurru Centre (Southbank University)</p>
  </div>
  <p class="year c2022" style="left:781px;top:627px;">2022</p>

  <div class="event c2023" style="left:953px;top:52px;width:200px;">
    <h3>Rebranding</h3>
    <p>Hollowmere rebranded</p>
  </div>
  <div class="event c2023" style="left:953px;top:95px;width:200px;">
    <h3>Reconciliation<br>Action Plan (RAP)</h3>
    <p>Hollowmere’s Reflect RAP<br>developed &amp; endorsed</p>
  </div>
  <div class="event c2023" style="left:953px;top:166px;width:200px;">
    <h3>Client Advisory Group</h3>
    <p>Hollowmere’s Client Advisory Group<br>commences</p>
  </div>
  <div class="event c2023" style="left:953px;top:221px;width:200px;">
    <h3>E-Learning Platform</h3>
    <p>Hollowmere e-learning<br>platform launched</p>
  </div>
  <div class="event c2023" style="left:953px;top:276px;width:200px;">
    <h3>Spectrum Mark</h3>
    <p>Hollowmere achieves<br>Spectrum Mark<br>accreditation</p>
  </div>
  <p class="year c2023" style="left:953px;top:334px;">2023</p>
</div>
</body>
</html>
```